Business Card Design

We like to use greens as you will see in our logo (but not TOO much green). We are a Dental Clinic in a somewhat eccentric community. We do not like the dated sharp designs which we see many dentists use. We're looking for something bright and fresh while still maintaining the integrity of the profession. Elegance is not necessarily what we are going for... we need for the design to be "mature" but also up-lifting.

See our logo.
Updates

Project Deadline Extended
Reason: We have 5 designs which we like. But we'd like to see a few more before committing to a design.

Project Deadline Extended
Reason: We are awaiting revisions to this project. We are still welcoming designs while we wait to see if designers are able to provide to us the revisions we require in order to proceed with a selection.

Target Market(s)

Younger families - ages late 20's to early 40's

Industry/Entity Type

Business

Contact Information for Business Card

Corwel T. Banfry DDS 2730 W. Halvert Rd. Ste. 7 Royal Oak, MI 48391 (248)555-0174 FX (248)555-0189 info@BrightwellDentalCareMi.com BrigthwellDentalCareMi.com on the back of the card we need an appointment reminder (For____ Date___ Time____) with "If you are unable to keep your appointment, kindly give 48 hours notice" at the bottom. No use of teeth in the design. DOUBLE SIDED DESIGN

Requirements
Should not have
• The use of pictures of teeth

```html
<!DOCTYPE html>
<html lang="en">
<head>
<meta charset="utf-8">
<title>Brightwell Dental Care – Business Card</title>
<link href="https://fonts.googleapis.com/css2?family=Source+Sans+3:wght@400;600;700&family=Tinos:ital,wght@0,400;0,700;1,400&display=swap" rel="stylesheet">
<style>
  :root {
    --bg: #ecebe6;
    --card: #ffffff;
    --green-dark: #2f7a1c;
    --green-lime: #a6d321;
    --ink: #444444;
    --rule: #777777;
    --white: #ffffff;
  }
  * { box-sizing: border-box; margin: 0; padding: 0; }
  html, body {
    width: 1200px; height: 492px; overflow: hidden;
    background: var(--bg);
    font-family: "Source Sans 3", Arial, sans-serif;
  }
  .sheet {
    position: relative; width: 1200px; height: 492px;
    display: flex; justify-content: center; align-items: center; gap: 50px;
  }
  .card {
    position: relative; width: 520px; height: 310px;
    background: var(--card); border-radius: 30px; overflow: hidden;
    box-shadow: 0 6px 18px rgba(0,0,0,.18);
  }

  /* Front */
  .brand-name {
    color: var(--green-dark); font-weight: 700; white-space: nowrap;
  }
  .card-front .brand-name {
    position: absolute; top: 62px; left: 0; right: 0; text-align: center;
    font-size: 36px; letter-spacing: .3px;
  }
  .contact-band {
    position: absolute; top: 150px; left: 0; right: 0; height: 116px;
    background: var(--green-lime);
    border-top: 3px solid var(--white);
    box-shadow: 0 -2px 0 var(--green-dark), 0 2px 0 var(--green-dark);
    display: flex; align-items: center;
  }
  .address {
    width: 262px; text-align: right; padding-right: 16px;
    color: var(--white); font-size: 14px; line-height: 1.3;
  }
  .band-divider { width: 1px; height: 88px; background: var(--white); }
  .contact-list { list-style: none; padding-left: 10px; color: var(--white); font-size: 14px; line-height: 1.55; }
  .contact-list li { display: flex; align-items: center; gap: 6px; }
  .contact-list svg { width: 13px; height: 13px; flex: none; }
  .doctor {
    position: absolute; top: 282px; left: 0; right: 0; text-align: center;
    transform: translateY(-50%);
    font-size: 22px; font-weight: 700; color: var(--green-dark);
  }
  .doctor .degree { color: var(--green-lime); font-size: 19px; }

  /* Back */
  .card-back .brand-name {
    position: absolute; top: 34px; left: 26px; font-size: 22px;
  }
  .back-rule {
    position: absolute; top: 68px; left: 26px; width: 340px;
    border-top: 1px dotted var(--rule);
  }
  .appt-title {
    position: absolute; top: 78px; left: 30px;
    font-family: "Tinos", "Times New Roman", serif; font-weight: 700;
    font-size: 17px; color: var(--green-dark); letter-spacing: .4px;
  }
  .field {
    position: absolute; font-size: 15px; color: var(--ink);
    display: flex; align-items: flex-end; gap: 6px;
  }
  .field .line { display: inline-block; border-bottom: 1px solid var(--rule); height: 1px; margin-bottom: 4px; }
  .field .line.dotted { border-bottom-style: dotted; }
  .box {
    display: inline-block; border: 1px solid var(--rule); border-radius: 3px;
    width: 28px; height: 20px; background: var(--white);
  }
  .box.wide { width: 94px; }
  .days {
    position: absolute; top: 236px; left: 30px; right: 20px;
    display: flex; align-items: center; gap: 6px;
    font-weight: 700; font-size: 14px; color: var(--ink);
  }
  .days .day { display: flex; align-items: center; gap: 5px; }
  .notice {
    position: absolute; bottom: 22px; left: 30px; right: 20px;
    font-family: "Tinos", "Times New Roman", serif; font-style: italic;
    font-size: 14.5px; color: var(--ink);
  }
</style>
</head>
<body>
<main class="sheet">

  <section class="card card-front" aria-label="Business card front">
    <div class="brand-name">Brightwell Dental Care</div>
    <div class="contact-band">
      <p class="address">2730 W. Halvert Rd. Ste.<br>7 Royal Oak, MI 48391</p>
      <span class="band-divider"></span>
      <ul class="contact-list">
        <li>
          <svg viewBox="0 0 16 16" aria-hidden="true"><path fill="#fff" d="M3.5 1.5l2.5 0 1 3.5-1.6 1.2a8 8 0 0 0 4.4 4.4L11 9l3.5 1v2.5c0 1-1 2-2 2A11 11 0 0 1 1.5 3.5c0-1 1-2 2-2z"/></svg>
          (248)555-0174
        </li>
        <li>
          <svg viewBox="0 0 16 16" aria-hidden="true"><rect x="4" y="1.5" width="8" height="5" fill="none" stroke="#fff" stroke-width="1.4"/><rect x="1.5" y="6" width="13" height="6" rx="1" fill="#fff"/><rect x="4" y="11" width="8" height="3.5" fill="#fff" stroke="#a6d321" stroke-width=".8"/></svg>
          (248)555-0189
        </li>
        <li>
          <svg viewBox="0 0 16 16" aria-hidden="true"><rect x="1.5" y="3.5" width="13" height="9" rx="1" fill="#fff"/><path d="M1.8 4l6.2 5 6.2-5" fill="none" stroke="#a6d321" stroke-width="1.3"/></svg>
          info@BrightwellDentalCareMi.com
        </li>
        <li>
          <svg viewBox="0 0 16 16" aria-hidden="true"><circle cx="8" cy="8" r="6.3" fill="none" stroke="#fff" stroke-width="1.3"/><ellipse cx="8" cy="8" rx="2.7" ry="6.3" fill="none" stroke="#fff" stroke-width="1.1"/><path d="M1.8 8h12.4" stroke="#fff" stroke-width="1.1"/></svg>
          www.BrigthwellDentalCareMi.com
        </li>
      </ul>
    </div>
    <p class="doctor">Corwel T. Banfry<span class="degree">, DDS</span></p>
  </section>

  <section class="card card-back" aria-label="Appointment card back">
    <div class="brand-name">Brightwell Dental Care</div>
    <div class="back-rule"></div>
    <h2 class="appt-title">YOUR APPOINTMENT</h2>

    <div class="field" style="top:112px; left:34px;">Name :<span class="line dotted" style="width:230px"></span></div>
    <div class="field" style="top:146px; left:34px;">Date :<span class="line" style="width:100px"></span></div>
    <div class="field" style="top:134px; left:190px;">Time :<span class="line" style="width:80px"></span>am / pm</div>
    <div class="field" style="top:160px; left:310px;"><span class="box wide"></span></div>
    <div class="field" style="top:190px; left:34px;">Next Appointment <span class="box wide"></span></div>

    <div class="days">
      <span class="day">MON <span class="box"></span></span>
      <span class="day">TUE <span class="box"></span></span>
      <span class="day">WED <span class="box"></span></span>
      <span class="day">THU <span class="box"></span></span>
      <span class="day">FRI <span class="box"></span></span>
      <span class="day">SAT <span class="box"></span></span>
    </div>
    <p class="notice">If you are unable to keep your appointment, kindly give 48 hours notice</p>
  </section>

</main>
</body>
</html>
```